Website for Vornelix Capital, my new firm that raises money from investors to buy, build, own an...

Vornelix Capital needs a website! We are a new company with very experienced people, who invest in, own and build hotel properties, as well as apartments and other commercial real estate. We seek investors for our projects, and we provide safe, secure returns on their investment in our projects. Our new logo is designed to exhibit strength, class and security, and would like our website to continue on this theme. Our name, Vornelix, is a word-play on a Greek word “aristeia”, which means “excellence” and “a warriors finest moment of glory in war”. If you are in business, you realize that much of it is like war, with strategy and moves and opponents and competitors, and ever-changing economic conditions and threats that make business very much like war. We like to think that we are good at business (war), and so have named our company “Vornelix”, using the founders last name and the word “aristeia” combined. Another definition of "aristeia" is "performing at the peak of one's potential after a long struggle"...again, much like business in real life! The website design should exhibit financial security, smart moves, and positive growth towards a bright future.

Target Market(s)

The target market is smart and wealthy investors, with others such as brokers, cities and government agencies, lenders, sellers, partners, etc also looking at it.

Industry/Entity Type

Investment

Number of Pages Required

5+ page

Font styles to use
Sans Serif

Colors
fec214

Requirements
Must have
• Our website should have a landing page, a "about" or bio page, a projects page and a contact us page. Our new logo uses the colors black and gold, so this should be factored in to our site. The site should be simple, yet impactful and impressive. I have actually two logos, which can be mixed and interchanged in a complimentary way, each with their own unique look.
Nice to have
• I have uploaded a couple screenshots of a website i like, and the simplicity I mention.
Should not have
• The site should not be flashy or complicated or complex or "busy"

```html
<!DOCTYPE html>
<html lang="en">
<head>
<meta charset="UTF-8">
<title>Vornelix Capital</title>
<link rel="stylesheet" href="https://fonts.googleapis.com/css2?family=Raleway:wght@400;500;600;700;800&family=Open+Sans:wght@400;600&display=swap">
<style>
:root{
  --gold:#fec214;
  --ink:#1e1e1e;
  --dark:#2f2f2f;
  --body:#555;
  --white:#fff;
  --map:#e4e4e2;
  --map-edge:#cfd0cd;
}
*{box-sizing:border-box;margin:0;padding:0}
html,body{width:1200px;height:3482px;overflow:hidden;background:var(--white)}
body{font-family:'Open Sans',sans-serif;color:var(--body)}
.page{position:relative;width:1200px;height:3482px;overflow:hidden}
.abs{position:absolute}

/* hero */
.hero{left:0;top:0;width:1200px;height:627px;background:linear-gradient(180deg,#3d4247 0%,#5b636b 45%,#2b2e31 100%)}
.brand{left:77px;top:30px;font-family:'Raleway',sans-serif;font-weight:600;font-size:24px;letter-spacing:1px;color:var(--white);display:flex;align-items:center;gap:10px}
.brand .bar{width:2px;height:30px;background:var(--white)}
.nav{font-family:'Raleway',sans-serif;font-size:14px;font-weight:500;color:var(--white)}
.nav a{color:var(--white);text-decoration:none;position:absolute;white-space:nowrap}
.nav a.active{color:var(--gold)}
.btn-contact-nav{left:966px;top:21px;width:156px;height:46px;border-radius:23px;background:var(--white);color:var(--ink);font-family:'Raleway',sans-serif;font-weight:700;font-size:15px;display:flex;align-items:center;justify-content:center}
.hero-title{left:0;top:256px;width:1200px;text-align:center;font-family:'Raleway',sans-serif;font-weight:800;font-size:42px;line-height:54px;color:var(--white);letter-spacing:.5px}
.hero-title span{color:var(--gold)}

/* about */
.h2{font-family:'Raleway',sans-serif;font-weight:600;font-size:40px;color:var(--ink)}
.about-title{left:79px;top:740px}
.about-text{left:79px;top:806px;width:400px;font-size:13px;line-height:25px}
.about-text p+p{margin-top:10px}
.btn-gold{background:var(--gold);color:var(--ink);font-family:'Raleway',sans-serif;font-weight:700;font-size:17px;border-radius:26px;display:flex;align-items:center;justify-content:center}
.about-btn{left:79px;top:1016px;width:188px;height:48px}
.about-photo{left:550px;top:796px;width:427px;height:272px;border-radius:10px;background:linear-gradient(135deg,#c9ccd1,#8e949c 55%,#5a5f66);box-shadow:0 10px 30px rgba(0,0,0,.25)}

/* services */
.service{width:330px;text-align:center}
.service h3{font-family:'Raleway',sans-serif;font-weight:500;font-size:21px;color:var(--ink);margin-bottom:18px}
.service p{font-size:13px;line-height:26px}

/* projects */
.projects{left:0;top:1699px;width:1200px;height:720px;background:var(--dark)}
.projects-title{left:0;top:1745px;width:1200px;text-align:center;color:var(--white)}
.proj-main{left:77px;top:1834px;width:501px;height:308px;background:linear-gradient(120deg,#f4ead0,#b7c3cf 45%,#4c5662)}
.proj-name{left:661px;top:1870px;font-family:'Raleway',sans-serif;font-weight:600;font-size:24px;color:var(--white)}
.proj-text{left:661px;top:1908px;width:470px;font-size:13px;line-height:26px;color:#e4e4e4}
.proj-text p+p{margin-top:10px}
.thumb{top:2182px;width:241px;height:146px}

/* testimonials */
.testi-title{left:79px;top:2502px}
.quote{left:77px;top:2570px}
.testi-text{left:79px;top:2632px;width:480px;font-size:13px;line-height:26px}
.testi-name{left:79px;top:2750px;font-family:'Raleway',sans-serif;font-weight:500;font-size:15px;color:var(--body)}
.dots{left:77px;top:2798px;display:flex;gap:10px}
.dots i{display:block;width:38px;height:4px;border-radius:2px;background:var(--gold);opacity:.45}
.dots i:first-child{opacity:1}
.world{left:560px;top:2480px;width:640px;height:417px;background:radial-gradient(ellipse at 60% 40%,#e6e6e6 0%,#f3f3f3 55%,#fff 80%)}
.person{left:600px;top:2480px;width:468px;height:417px;background:radial-gradient(ellipse 48% 55% at 55% 52%,#5a5f52 0%,#8a8a80 45%,rgba(230,228,224,.6) 75%,rgba(255,255,255,0) 100%)}

/* map + newsletter */
.map{left:0;top:2897px;width:1200px;height:422px;background:linear-gradient(180deg,var(--map) 0%,#e0e1de 60%,var(--map-edge) 100%)}
.tip{left:794px;top:2976px;width:237px;height:116px;background:var(--white);border-radius:6px;box-shadow:0 4px 14px rgba(0,0,0,.2);text-align:center;font-size:15px;line-height:26px;color:var(--ink);display:flex;align-items:center;justify-content:center;padding:0 20px}
.tip-arrow{left:902px;top:3091px}
.pin-ring{left:896px;top:3119px;width:28px;height:28px;border-radius:50%;background:rgba(254,194,20,.3)}
.pin{left:903px;top:3126px;width:14px;height:14px;border-radius:50%;background:var(--gold)}
.map-zoom{left:1155px;top:3203px;width:30px;height:61px;background:var(--white);border-radius:3px;box-shadow:0 1px 4px rgba(0,0,0,.25)}
.map-person{left:1155px;top:3272px;width:30px;height:30px;background:var(--white);border-radius:3px;box-shadow:0 1px 4px rgba(0,0,0,.25)}
.map-layer{left:18px;top:3240px;width:46px;height:60px;border:2px solid var(--white);border-radius:3px;background:linear-gradient(160deg,#7b8a6a,#4a5a44);box-shadow:0 1px 4px rgba(0,0,0,.25)}
.footer{left:0;top:3319px;width:1200px;height:163px;background:var(--dark)}
.footer p{position:absolute;left:0;top:117px;width:1200px;text-align:center;font-size:12px;color:#ddd}
.news{left:77px;top:3242px;width:1046px;height:165px;background:var(--white);border-radius:12px;box-shadow:0 6px 24px rgba(0,0,0,.12)}
.news p{position:absolute;left:0;top:40px;width:1046px;text-align:center;font-size:13px}
.news-field{left:330px;top:3312px;width:541px;height:46px;border:2px solid var(--gold);border-radius:24px;font-size:13px;color:#777;padding:13px 22px}
.news-btn{left:712px;top:3312px;width:159px;height:46px;font-size:19px;font-weight:800}
</style>
</head>
<body>
<div class="page">

  <header class="abs hero" role="img" aria-label="Photo of business people walking past a glass office building"></header>
  <div class="abs brand">VORNELIX<span class="bar"></span>CAPITAL</div>
  <nav class="abs nav" style="left:0;top:34px;width:1200px">
    <a class="active" style="left:594px">HOME</a>
    <a style="left:673px">ABOUT</a>
    <a style="left:761px">PROJECTS</a>
    <a style="left:871px">CONTACT</a>
  </nav>
  <div class="abs btn-contact-nav">CONTACT US</div>
  <h1 class="abs hero-title">VORNELIX CAPITAL FOR <span>SAFE</span><br>AND <span>SECURE</span> RETURNS</h1>

  <svg class="abs" style="left:0;top:700px" width="1200" height="470" viewBox="0 700 1200 470">
    <rect x="760" y="715" width="500" height="434" rx="40" fill="#fec214"/>
    <rect x="690" y="776" width="160" height="26" rx="13" fill="#fec214"/>
    <rect x="650" y="1068" width="200" height="26" rx="13" fill="#fec214"/>
    <rect x="674" y="1100" width="180" height="49" rx="24" fill="#fec214"/>
  </svg>

  <h2 class="abs h2 about-title">About us</h2>
  <div class="abs about-text">
    <p>Lorem Ipsum is simply dummy text of the printing and typesetting industry. Lorem Ipsum has been the industry's standard dummy text ever since the 1500s, when an unknown printer took a galley of type and scrambled it to make a type specimen book.</p>
    <p>It was popularised in the 1960s with the release of Typeline sheets containing Lorem Ipsum passages.</p>
  </div>
  <div class="abs btn-gold about-btn">CONTACT US</div>
  <div class="abs about-photo" role="img" aria-label="Photo of business partners reviewing documents in a busy plaza"></div>

  <svg class="abs" style="left:0;top:1230px" width="1200" height="260" viewBox="0 1230 1200 260">
    <path d="M0 1323 C 110 1300 170 1380 239 1376 S 470 1398 599 1407 S 850 1455 961 1400 S 1110 1230 1200 1282" fill="none" stroke="#fec214" stroke-width="5"/>
    <g fill="none" stroke="#fec214" stroke-opacity=".35" stroke-width="1.5">
      <circle cx="239" cy="1376" r="38"/><circle cx="599" cy="1407" r="38"/><circle cx="961" cy="1400" r="38"/>
    </g>
    <g fill="#fec214">
      <circle cx="239" cy="1376" r="9"/><circle cx="599" cy="1407" r="9"/><circle cx="961" cy="1400" r="9"/>
    </g>
  </svg>

  <div class="abs service" style="left:74px;top:1517px"><h3>Hotel properties</h3><p>Lorem Ipsum is simply dummy text of the printing and typesetting industry Lorem Ipsum.</p></div>
  <div class="abs service" style="left:434px;top:1517px"><h3>Apartments</h3><p>Lorem Ipsum is simply dummy text of the printing and typesetting industry Lorem Ipsum.</p></div>
  <div class="abs service" style="left:796px;top:1517px"><h3>Commercial real estate</h3><p>Lorem Ipsum is simply dummy text of the printing and typesetting industry Lorem Ipsum.</p></div>

  <section class="abs projects"></section>
  <h2 class="abs h2 projects-title">Recent Projects</h2>
  <div class="abs proj-main" role="img" aria-label="Photo of a businesswoman among sunlit city towers"></div>
  <h3 class="abs proj-name">PROJECT NAME</h3>
  <div class="abs proj-text">
    <p>Lorem Ipsum is simply dummy text of the printing and typesetting industry. Lorem Ipsum has been the industry's standard dummy text ever since the 1500s, when an unknown printer took a galley of type and scrambled it to make a type specimen book.</p>
    <p>It was popularised in the 1960s with the release of Typeline sheets containing Lorem Ipsum passages, and more recently with desktop publishing software like Quillset Layout including versions of Lorem.</p>
  </div>
  <div class="abs thumb" style="left:77px;background:linear-gradient(160deg,#2d5f9a,#8fb6dc)" role="img" aria-label="Photo looking up at glass skyscrapers"></div>
  <div class="abs thumb" style="left:346px;background:linear-gradient(160deg,#e8ecef,#9aa5ad)" role="img" aria-label="Photo of a meeting in a bright office"></div>
  <div class="abs thumb" style="left:615px;background:linear-gradient(160deg,#6e8fb8,#2c3e57)" role="img" aria-label="Photo of a modern glass building facade"></div>
  <div class="abs thumb" style="left:882px;background:linear-gradient(160deg,#cfc9c0,#5e5850)" role="img" aria-label="Photo of a team working at an office table"></div>

  <div class="abs world" role="img" aria-label="Faint dotted world map backdrop"></div>
  <div class="abs person" role="img" aria-label="Photo of a man holding a laptop"></div>
  <h2 class="abs h2 testi-title">Testimonials</h2>
  <svg class="abs quote" width="52" height="44" viewBox="0 0 52 44">
    <path d="M0 44V26C0 12 7 4 20 0l2 6C14 9 11 14 11 20h10v24zM30 44V26C30 12 37 4 50 0l2 6C44 9 41 14 41 20h10v24z" fill="#fec214"/>
  </svg>
  <p class="abs testi-text">Lorem Ipsum is simply dummy text of the printing and typesetting industry. Lorem Ipsum has been the industry's standard dummy text ever since the 1500s, when an unknown printer took a galley of type and scrambled it to make a type specimen book. It has survived not only five centuries.</p>
  <p class="abs testi-name">- NAME SURNAME</p>
  <div class="abs dots"><i></i><i></i><i></i></div>

  <div class="abs map" role="img" aria-label="Road map of the region around the office"></div>
  <div class="abs tip">Lorem Ipsum is simply dummy text of the printing.</div>
  <svg class="abs tip-arrow" width="16" height="10" viewBox="0 0 16 10"><path d="M0 0h16L8 10z" fill="#fff"/></svg>
  <div class="abs pin-ring"></div>
  <div class="abs pin"></div>
  <div class="abs map-layer" role="img" aria-label="Satellite view toggle"></div>
  <svg class="abs map-zoom" width="30" height="61" viewBox="0 0 30 61">
    <path d="M9 15h12M15 9v12M9 46h12" stroke="#666" stroke-width="2.5" stroke-linecap="round"/>
    <path d="M6 30.5h18" stroke="#e2e2e2" stroke-width="1"/>
  </svg>
  <svg class="abs map-person" width="30" height="30" viewBox="0 0 30 30">
    <circle cx="15" cy="9" r="3.5" fill="#999"/>
    <rect x="11" y="13.5" width="8" height="11" rx="3" fill="#999"/>
  </svg>

  <footer class="abs footer"><p>©VORNELIX CAPITAL. 2018 · All Rights Reserved.</p></footer>
  <div class="abs news"><p>Subscribe to our newsletter to get more info and lates update</p></div>
  <div class="abs news-field">Enter your email</div>
  <div class="abs btn-gold news-btn">SUBSCRIBE</div>

</div>
</body>
</html>
```